Explosive, chemical reaction of creativity!

Web design for a digital marketing company. The unconventional is encouraged!
This is for a cool, young, geographically diverse company (sketchhive... you are all part of our team!!!)... we build websites but our real specialty is "search experience optimization".... creating conversion focused content, SEO (including content), and social media.

Target Market(s)

small to medium size businesses, law firms, medical practices, municipalities

Industry/Entity Type

Marketing

Number of Pages Required

2 page

Requirements
Must have
• WOW
• something different and special... we've been playing with a science theme (www.fernquillmedia.marketing) but we are open to different looks, layouts, etc.
• we nee a homepage design and an interior page design
• content needs to include: Marketing Catalysts (about us), Our Formula (services), Chemical Reactions(Results/Our Clients),
• FREE Online Prism Check
• Let us put together an objective snapshot of your digital presence for you.
Nice to have
• we are open to the use of background video (chemical reaction???)
• we are open to cool and different imagery
Should not have
• template look like most other websites

```html
<!DOCTYPE html>
<html lang="en">
<head>
<meta charset="utf-8">
<title>Fernquill Media — Digital Marketing</title>
<link rel="stylesheet" href="https://fonts.googleapis.com/css2?family=Oswald:wght@300;400;700&family=Roboto:wght@300;400;500;700&display=swap">
<style>
  :root {
    --cobalt: #0b4ea2;
    --cobalt-deep: #083c80;
    --ink: #2f2f2f;
    --text: #555555;
    --muted: #8a8a8a;
    --ring-grey: #d9d9d9;
    --band-grey: #f2f2f2;
    --rule: #e3e3e3;
    --white: #ffffff;
    --black: #111111;
  }
  * { box-sizing: border-box; margin: 0; padding: 0; }
  html, body { width: 1200px; height: 2528px; overflow: hidden; }
  body { position: relative; background: var(--white); font-family: 'Roboto', Arial, sans-serif; color: var(--ink); }
  .abs { position: absolute; }

  /* Header */
  .site-header { position: absolute; left: 0; top: 0; width: 1200px; height: 127px; background: var(--white); border-bottom: 3px solid var(--cobalt); }
  .utility-bar { position: absolute; top: 14px; right: 98px; display: flex; align-items: center; gap: 8px; font-size: 13px; color: #555; }
  .utility-bar .label { margin-right: 6px; }
  .social-mini { width: 25px; height: 25px; border: 1px solid #cfcfcf; background: #fff; }
  .utility-bar .user-link { margin-left: 20px; display: flex; align-items: center; gap: 8px; }
  .brand { position: absolute; left: 101px; top: 48px; display: flex; align-items: center; gap: 12px; }
  .brand-mark { width: 30px; height: 30px; background: var(--cobalt); }
  .brand-name { font-family: 'Roboto', Arial, sans-serif; font-weight: 700; font-size: 21px; letter-spacing: 2px; color: var(--cobalt-deep); text-transform: uppercase; }
  .main-nav-bg { position: absolute; left: 0; top: 0; }
  .main-nav { position: absolute; top: 54px; left: 498px; height: 73px; display: flex; align-items: center; gap: 27px; }
  .main-nav a { color: var(--white); text-decoration: none; font-size: 13px; font-weight: 400; letter-spacing: 0; text-transform: uppercase; }
  .main-nav a.active { font-weight: 500; }

  /* Hero */
  .hero { position: absolute; left: 0; top: 127px; width: 1200px; height: 577px;
    background: radial-gradient(ellipse at 70% 30%, #8a96a6 0%, #5f6a78 35%, #3b4350 70%, #2a3039 100%); }
  .hero-shade { position: absolute; inset: 0; background: rgba(20,30,45,.35); }
  .hero-title { position: absolute; top: 258px; width: 100%; text-align: center; color: var(--white); font-family: 'Oswald', Arial, sans-serif; line-height: 1.15; }
  .hero-title .line-strong { display: block; font-size: 48px; font-weight: 400; }
  .hero-title .line-light { display: block; font-size: 44px; font-weight: 300; }
  .hero-sub { position: absolute; top: 372px; left: 320px; width: 560px; text-align: center; color: #eef1f5; font-size: 17px; font-weight: 300; line-height: 26px; }
  .slider-arrow { position: absolute; top: 271px; width: 37px; height: 37px; }

  /* Formula */
  .formula { position: absolute; left: 0; top: 704px; width: 1200px; height: 420px; background: var(--band-grey); }
  .section-title { font-size: 26px; font-weight: 400; color: var(--ink); text-transform: uppercase; text-align: center; }
  .formula .section-title { position: absolute; top: 42px; width: 100%; }
  .formula .lede { position: absolute; top: 80px; width: 100%; text-align: center; font-size: 17px; color: #555; }
  .formula-item { position: absolute; top: 139px; width: 260px; text-align: center; }
  .formula-icon { width: 131px; height: 131px; margin: 0 auto; }
  .formula-item h3 { margin-top: 22px; font-size: 16px; font-weight: 500; letter-spacing: .5px; color: var(--ink); }
  .formula-item p { margin: 14px auto 0; width: 252px; font-size: 11.5px; line-height: 21px; color: var(--muted); }
  .side-chevron { position: absolute; top: 872px; width: 34px; height: 102px; }

  /* Prism check */
  .prism-check { position: absolute; left: 0; top: 1124px; width: 1200px; height: 278px;
    background: radial-gradient(ellipse at 50% 40%, #18223a 0%, #0b0f1c 60%, #05070d 100%); color: var(--white); text-align: center; }
  .prism-check h2 { position: absolute; top: 46px; width: 100%; font-size: 26px; font-weight: 500; text-transform: uppercase; }
  .prism-check p { position: absolute; top: 95px; left: 176px; width: 848px; font-size: 11.5px; line-height: 21px; color: #d8dce4; }
  .btn-cobalt { position: absolute; left: 522px; top: 187px; width: 156px; height: 38px; background: var(--cobalt); color: var(--white); font-size: 13px; line-height: 38px; text-transform: uppercase; letter-spacing: .5px; }

  /* Data */
  .data-success { position: absolute; left: 0; top: 1402px; width: 1200px; height: 536px; background: var(--white); }
  .data-success h2 { position: absolute; left: 99px; top: 36px; font-size: 25px; font-weight: 500; color: var(--ink); text-transform: uppercase; }
  .data-success .subhead { position: absolute; left: 99px; top: 78px; width: 420px; font-size: 17.5px; line-height: 25px; color: #444; }
  .data-success .body-copy { position: absolute; left: 99px; top: 144px; width: 560px; font-size: 11.5px; line-height: 19px; color: var(--muted); }
  .marketing-art { position: absolute; left: 750px; top: 27px; width: 325px; height: 240px; border-radius: 50%;
    background: radial-gradient(circle at 50% 50%, #f3c45a 0%, #7fa6d8 45%, #e9eef6 75%, rgba(255,255,255,0) 100%); }
  .stat { position: absolute; top: 291px; width: 250px; text-align: center; }
  .stat-ring { width: 142px; height: 142px; margin: 0 auto; display: block; }
  .stat-caption { margin: 20px auto 0; width: 216px; font-size: 15.5px; line-height: 24px; color: #555; font-weight: 300; }

  /* Snapshot */
  .snapshot { position: absolute; left: 0; top: 1938px; width: 1200px; height: 323px;
    background: linear-gradient(100deg, #0a3a7c 0%, #155fb8 45%, #2a6fc2 60%, #0c438c 100%); color: var(--white); text-align: center; }
  .snapshot h2 { position: absolute; top: 48px; left: 260px; width: 680px; font-size: 24.5px; font-weight: 500; line-height: 35px; text-transform: uppercase; }
  .snapshot p { position: absolute; top: 130px; left: 99px; width: 1002px; font-size: 11.5px; line-height: 19px; color: #e4ecf7; }
  .btn-dark { position: absolute; left: 531px; top: 237px; width: 138px; height: 38px; background: var(--black); color: var(--white); font-size: 13px; line-height: 38px; text-transform: uppercase; }

  /* Footer */
  .site-footer { position: absolute; left: 0; top: 2261px; width: 1200px; height: 267px; background: var(--white); }
  .footer-heading { font-size: 17px; font-weight: 500; color: var(--ink); }
  .footer-contact { position: absolute; left: 101px; top: 42px; }
  .footer-contact address { font-style: normal; margin-top: 22px; font-size: 13.5px; line-height: 28px; color: var(--muted); }
  .contact-line { display: flex; align-items: center; gap: 10px; font-size: 14px; color: #444; line-height: 24px; }
  .newsletter { position: absolute; left: 435px; top: 42px; }
  .newsletter-form { position: absolute; top: 44px; left: 0; width: 350px; height: 44px; display: flex; }
  .newsletter-input { width: 242px; height: 44px; border: 1px solid #cfcfcf; border-right: none; border-radius: 6px 0 0 6px; font-size: 13px; color: #999; line-height: 42px; padding-left: 14px; }
  .newsletter-btn { width: 108px; height: 44px; background: #2b2b2b; color: #fff; border-radius: 6px; font-size: 14px; font-weight: 500; line-height: 44px; text-align: center; text-transform: uppercase; margin-left: -6px; }
  .footer-links { position: absolute; right: 101px; top: 42px; text-align: right; }
  .social-row { position: absolute; right: 98px; top: 93px; display: flex; gap: 13px; }
  .social-box { width: 38px; height: 38px; border: 1px solid #777; }
  .legal-links { position: absolute; right: 101px; top: 158px; text-align: right; font-size: 12.5px; line-height: 20px; color: var(--muted); }
  .copyright { position: absolute; left: 0; top: 2470px; width: 1200px; border-top: 1px solid var(--rule); text-align: center; font-size: 11.5px; color: var(--muted); padding-top: 11px; }
  .bottom-strip { position: absolute; left: 0; top: 2520px; width: 1200px; height: 8px; background: #2a2a2a; }
</style>
</head>
<body>

<header class="site-header">
  <svg class="main-nav-bg" width="1200" height="127" viewBox="0 0 1200 127" aria-hidden="true">
    <polygon points="430,127 463,54 1200,54 1200,127" fill="#0b4ea2"/>
  </svg>
  <div class="utility-bar">
    <span class="label">Our User :</span>
    <span class="social-mini"></span><span class="social-mini"></span><span class="social-mini"></span><span class="social-mini"></span>
    <span class="user-link">
      <svg width="12" height="13" viewBox="0 0 12 13" aria-hidden="true"><circle cx="6" cy="3.5" r="3" fill="#0b4ea2"/><path d="M0 13 Q0 7 6 7 Q12 7 12 13Z" fill="#0b4ea2"/></svg>
      User Area&nbsp;&nbsp;/&nbsp;&nbsp;Contact Us
    </span>
  </div>
  <div class="brand">
    <span class="brand-mark"></span>
    <span class="brand-name">Fernquill Media</span>
  </div>
  <nav class="main-nav">
    <a class="active" href="#">Home</a>
    <a href="#">Marketing Catalysts</a>
    <a href="#">Our Formula</a>
    <a href="#">Chemical Reactions</a>
    <a href="#">Contact Us</a>
  </nav>
</header>

<section class="hero">
  <div class="abs" style="inset:0" role="img" aria-label="Photo of a team working together at laptops on a desk"></div>
  <div class="hero-shade"></div>
  <svg class="slider-arrow" style="left:60px" viewBox="0 0 37 37" aria-hidden="true"><circle cx="18.5" cy="18.5" r="17" fill="none" stroke="rgba(255,255,255,.6)" stroke-width="2"/><path d="M21 11 L14 18.5 L21 26" fill="none" stroke="rgba(255,255,255,.8)" stroke-width="2.5"/></svg>
  <svg class="slider-arrow" style="left:1101px" viewBox="0 0 37 37" aria-hidden="true"><circle cx="18.5" cy="18.5" r="17" fill="none" stroke="rgba(255,255,255,.6)" stroke-width="2"/><path d="M16 11 L23 18.5 L16 26" fill="none" stroke="rgba(255,255,255,.8)" stroke-width="2.5"/></svg>
  <h1 class="hero-title"><span class="line-strong">IT'S NOT ROCKET SCIENCE, IT'S</span><span class="line-light">FERNQUILL MEDIA SCIENCE!</span></h1>
  <p class="hero-sub">Sales is the chemical reaction that results from "our formula" which is the right combination of our digital marketing services.</p>
</section>

<section class="formula">
  <h2 class="section-title">The Perfect Digital Marketing Formula!</h2>
  <p class="lede">Get the right message in front of the right people.</p>

  <div class="formula-item" style="left:106px">
    <svg class="formula-icon" viewBox="0 0 131 131" aria-hidden="true">
      <circle cx="65.5" cy="65.5" r="65" fill="#0b4ea2"/><circle cx="65.5" cy="65.5" r="55" fill="none" stroke="#fff" stroke-width="3"/>
      <g fill="none" stroke="#fff" stroke-width="3"><circle cx="65.5" cy="65.5" r="24"/><ellipse cx="65.5" cy="65.5" rx="10" ry="24"/><line x1="41.5" y1="65.5" x2="89.5" y2="65.5"/><path d="M45 53 H86 M45 78 H86"/></g>
    </svg>
    <h3>WEBSITE</h3>
    <p>You've got 10 seconds to grab the attention of a site viewer. We build for appearance, content, and functionality. It's a conversion.</p>
  </div>
  <div class="formula-item" style="left:472px">
    <svg class="formula-icon" viewBox="0 0 131 131" aria-hidden="true">
      <circle cx="65.5" cy="65.5" r="65" fill="#0b4ea2"/><circle cx="65.5" cy="65.5" r="55" fill="none" stroke="#fff" stroke-width="3"/>
      <rect x="48" y="42" width="34" height="46" fill="none" stroke="#fff" stroke-width="3"/>
      <g stroke="#fff" stroke-width="3"><line x1="55" y1="53" x2="75" y2="53"/><line x1="55" y1="61" x2="75" y2="61"/><line x1="55" y1="69" x2="75" y2="69"/><line x1="55" y1="77" x2="70" y2="77"/></g>
    </svg>
    <h3>CONTENT</h3>
    <p>Content is the most powerful element of our formula... it creates need, provokes emotion and sparks action.</p>
  </div>
  <div class="formula-item" style="left:832px">
    <svg class="formula-icon" viewBox="0 0 131 131" aria-hidden="true">
      <circle cx="65.5" cy="65.5" r="65" fill="#0b4ea2"/><circle cx="65.5" cy="65.5" r="55" fill="none" stroke="#fff" stroke-width="3"/>
      <path d="M50 42 H81 V55 Q81 72 65.5 74 Q50 72 50 55 Z" fill="#fff"/>
      <path d="M50 46 H42 Q42 60 52 62 M81 46 H89 Q89 60 79 62" fill="none" stroke="#fff" stroke-width="3"/>
      <rect x="62" y="73" width="7" height="10" fill="#fff"/><rect x="53" y="83" width="25" height="7" fill="#fff"/>
    </svg>
    <h3>SOCIAL</h3>
    <p>We are obsessed with the latest trends and are always testing new ways to cultivate both following and engagement.</p>
  </div>
</section>
<svg class="side-chevron" style="left:52px" viewBox="0 0 34 102" aria-hidden="true"><path d="M32 2 L3 51 L32 100" fill="none" stroke="#d2d2d2" stroke-width="2"/></svg>
<svg class="side-chevron" style="left:1114px" viewBox="0 0 34 102" aria-hidden="true"><path d="M2 2 L31 51 L2 100" fill="none" stroke="#d2d2d2" stroke-width="2"/></svg>

<section class="prism-check">
  <div class="abs" style="inset:0" role="img" aria-label="Dark background of glowing connected network lines"></div>
  <h2>Free Online Prism Check</h2>
  <p>Pleasure and praising pain was born and I will give you a complete account of the system, and expound the actual teachings of the great explorer of the truth, the master-builder of human happiness. No one rejects, dislikes, or avoids pleasure itself, because it is pleasure, but because those who do not know how to pursue pleasure rationally encounter consequences that are extremely painful. Nor again is there anyone who loves or pursues or desires to obtain</p>
  <div class="btn-cobalt">Go Free Digital</div>
</section>

<section class="data-success">
  <h2>Using Data for Success</h2>
  <p class="subhead">Search Engine Optimization has been replaced with Search Experience Optimization.</p>
  <p class="body-copy">There's been a lot of talk the last few years about SEO, Search Engine Optimization. We believe that Search Engine Optimization has now been replaced with Search Experience Optimization. That's right, we said it. We optimize for the users search experience which makes logical sense and now is "rewarded" by Querra and the other search engines. We create quality content, a great mobile experience and we are driven by user experience metrics.</p>
  <div class="marketing-art" role="img" aria-label="Illustration of a megaphone surrounded by marketing icons"></div>

  <div class="stat" style="left:72px">
    <svg class="stat-ring" viewBox="0 0 142 142" aria-hidden="true">
      <circle cx="71" cy="71" r="65" fill="none" stroke="#d9d9d9" stroke-width="8"/>
      <circle cx="71" cy="71" r="65" fill="none" stroke="#0b4ea2" stroke-width="8" stroke-dasharray="379.8 408.4" transform="translate(71 71) rotate(90) scale(-1 1) translate(-71 -71)"/>
      <text x="71" y="88" text-anchor="middle" font-family="Oswald, Arial, sans-serif" font-weight="700" font-size="50" fill="#1a1a1a">93<tspan font-size="28" font-weight="300">%</tspan></text>
    </svg>
    <p class="stat-caption">Online experiences begin with a search engine</p>
  </div>
  <div class="stat" style="left:340px">
    <svg class="stat-ring" viewBox="0 0 142 142" aria-hidden="true">
      <circle cx="71" cy="71" r="65" fill="none" stroke="#d9d9d9" stroke-width="8"/>
      <circle cx="71" cy="71" r="65" fill="none" stroke="#0b4ea2" stroke-width="8" stroke-dasharray="285.9 408.4" transform="translate(71 71) rotate(90) scale(-1 1) translate(-71 -71)"/>
      <text x="71" y="88" text-anchor="middle" font-family="Oswald, Arial, sans-serif" font-weight="700" font-size="50" fill="#1a1a1a">70<tspan font-size="28" font-weight="300">%</tspan></text>
    </svg>
    <p class="stat-caption">Of the links search users click on are organic</p>
  </div>
  <div class="stat" style="left:608px">
    <svg class="stat-ring" viewBox="0 0 142 142" aria-hidden="true">
      <circle cx="71" cy="71" r="65" fill="none" stroke="#d9d9d9" stroke-width="8"/>
      <circle cx="71" cy="71" r="65" fill="none" stroke="#0b4ea2" stroke-width="8" stroke-dasharray="285.9 408.4" transform="translate(71 71) rotate(90) scale(-1 1) translate(-71 -71)"/>
      <text x="71" y="88" text-anchor="middle" font-family="Oswald, Arial, sans-serif" font-weight="700" font-size="50" fill="#1a1a1a">70<tspan font-size="28" font-weight="300">%</tspan></text>
    </svg>
    <p class="stat-caption">Of US population has at least one social networking profile</p>
  </div>
  <div class="stat" style="left:876px">
    <svg class="stat-ring" viewBox="0 0 142 142" aria-hidden="true">
      <circle cx="71" cy="71" r="65" fill="none" stroke="#d9d9d9" stroke-width="8"/>
      <circle cx="71" cy="71" r="65" fill="none" stroke="#0b4ea2" stroke-width="8" stroke-dasharray="204.2 408.4" transform="translate(71 71) rotate(90) scale(-1 1) translate(-71 -71)"/>
      <text x="71" y="88" text-anchor="middle" font-family="Oswald, Arial, sans-serif" font-weight="700" font-size="50" fill="#1a1a1a">50<tspan font-size="28" font-weight="300">%</tspan></text>
    </svg>
    <p class="stat-caption">Of companies are using digital marketing but don't have a</p>
  </div>
</section>

<section class="snapshot">
  <div class="abs" style="inset:0" role="img" aria-label="Blue-tinted photo of a person touching a screen of connected icons"></div>
  <h2>Let us put together an objective snapshot of<br>your digital presence for you</h2>
  <p>Accusamus et iusto odio dignissimos ducimus qui blanditiis praesentium voluptatum deleniti atque corrupti quos dolores et quas molestias excepturi sint occaecati cupiditate non provident, similique sunt in culpa qui officia deserunt mollitia animi, id est laborum et dolorum fuga. Et harum quidem rerum facilis est et expedita distinctio. Nam libero tempore, cum soluta nobis est eligendi optio cumque nihil impedit quo minus id quod maxime placeat facere possimus, omnis voluptas assumenda est, omnis dolor repellendus. Temporibus autem quibusdam et aut officiis debitis aut rerum necessitatibus saepe eveniet ut et voluptates repudiandae sint et molestiae non recusandae.</p>
  <div class="btn-dark">Go Free Digital</div>
</section>

<footer class="site-footer">
  <div class="footer-contact">
    <h4 class="footer-heading">Contact Us</h4>
    <address>2760 W. Orchard Avenue<br>Suite 410, Brightwater, TX 78930</address>
    <div class="contact-line" style="margin-top:8px">
      <svg width="13" height="13" viewBox="0 0 13 13" aria-hidden="true"><path d="M2 0 L5 0 L6 3.5 L4.2 5 Q5.5 7.8 8 8.8 L9.5 7 L13 8 L13 11 Q13 13 11 13 Q0 12 0 2 Q0 0 2 0Z" fill="#333"/></svg>
      555-318-4062
    </div>
    <div class="contact-line">
      <svg width="13" height="11" viewBox="0 0 13 11" aria-hidden="true"><rect x="0" y="0" width="13" height="11" fill="#333"/><path d="M0 1 L6.5 6 L13 1" fill="none" stroke="#fff" stroke-width="1.3"/></svg>
      info@fernquillmedia.marketing
    </div>
  </div>
  <div class="newsletter">
    <h4 class="footer-heading">Join our newsletter!</h4>
    <div class="newsletter-form">
      <div class="newsletter-input">Enter Email*</div>
      <div class="newsletter-btn">Subscribe</div>
    </div>
  </div>
  <div class="footer-links"><h4 class="footer-heading">About Us&nbsp;&nbsp;/&nbsp;&nbsp;Contact Us</h4></div>
  <div class="social-row">
    <span class="social-box"></span><span class="social-box"></span><span class="social-box"></span><span class="social-box"></span><span class="social-box"></span>
  </div>
  <div class="legal-links">Privacy &amp; Cookie Policy<br>Terms &amp; Conditions</div>
</footer>
<div class="copyright">© Copyright 2016 fernquillmedia.marketing.com</div>
<div class="bottom-strip"></div>

</body>
</html>
```